Sparkling Wine Label Mirren Hollow

Super Premium Sparkling Wine Label

We are a super premium tasmanian fine wine producer and are about to release our first Sparking Wine.

please visit www.mirrenhollow-example.com.au to check out our range of wine. We need a label that will sit within this branding but as the aspirational product. We think that the Vosse grey/navy label will fit into this concept. It is masculine clean elegent and very smick,
and would be a great addition to our line see Argent Pinot Noir label.

However you can be quite creative with Sparkling Line eg Belvane Royal Cuvee is a stunning classical french label featuring gold baroque detail and feminine elegence.

Its up to you if you where spending $50 on a special bottles of sparkling wine what would you expect to see?

Black/Gold Graphite/Gold

Needs a neck /collar label

Main Front Label
Mirren Hollow
Chardonnay Pinot Noir
Tasmania

Back label has all the techical into you can use the back label from existing labels but reverserve out the colours to black and white or graphite and white

We want a label that oozes quality and expense. That says this the way I want to celebrate.

Target Market(s)

40 60 age group appreciator of quality

Industry/Entity Type

Product

Requirements
Must have
• Neck label
Simular to Vosse Shield so
MIRREN arched above
G rondel in middle possibiliy replacing coat of arms
TASMANIA arched under in red

Main Front Label
Mirren Hollow
Tasmania
Chardonnay Pinot Noir 750ML

Back Label / use the attachment Mirren label just reverse out so that it is a black label with white writing and amend information
Mirren Hollow
23 Pell Morrow Rd Ashvale
Tasmania, 7261
0412557390
www.mirrenhollow-example.com.au
contact@mirrenhollow-example.com.au
Sulphur Dioxide Added
Alc/Vol 12.5%
7.7 Standard Drinks

Rondel g

```html
<!DOCTYPE html>
<html lang="en">
<head>
<meta charset="utf-8">
<title>Mirren Hollow Sparkling Labels</title>
<link rel="stylesheet" href="https://fonts.googleapis.com/css2?family=Cormorant+Garamond:wght@500&family=Libre+Caslon+Text&family=Arimo&display=swap">
<style>
  :root {
    --bg-light: #f4f4f5;
    --bg-dark: #c9cacd;
    --navy: #1d2352;
    --navy-deep: #121638;
    --navy-bar: #20287a;
    --silver-light: #e4e5e7;
    --silver-mid: #c3c5c8;
    --silver-dark: #a9abaf;
    --ink: #2b2b2e;
    --ink-soft: #4a4b50;
    --rule: #e9eaee;
  }
  * { margin: 0; padding: 0; box-sizing: border-box; }
  html, body { width: 1200px; height: 1000px; overflow: hidden; }
  body {
    background: radial-gradient(ellipse at 55% 40%, var(--bg-light) 0%, var(--bg-dark) 100%);
    position: relative;
    font-family: "Libre Caslon Text", Georgia, serif;
  }

  /* Neck collar */
  .neck-collar {
    position: absolute;
    left: 150px; top: 150px;
    width: 900px; height: 104px;
    background: linear-gradient(180deg, var(--navy) 0%, var(--navy-deep) 100%);
  }
  .neck-collar::before,
  .neck-collar::after {
    content: "";
    position: absolute; left: 0; right: 0;
    height: 3px;
    background: var(--silver-mid);
  }
  .neck-collar::before { top: 10px; }
  .neck-collar::after { bottom: 10px; }

  .neck-medallion {
    position: absolute;
    left: 455px; top: 52px;
    width: 290px; height: 290px;
  }

  /* Front label */
  .front-label {
    position: absolute;
    left: 300px; top: 440px;
    width: 600px; height: 420px;
    background: linear-gradient(100deg, var(--silver-dark) 0%, var(--silver-light) 35%, var(--silver-mid) 65%, var(--silver-light) 100%);
  }
  .front-label__frame {
    position: absolute; inset: 12px;
    border: 1px solid var(--rule);
  }
  .front-label__bar {
    position: absolute;
    left: 74px; top: 12px;
    width: 6px; height: 260px;
    background: var(--navy-bar);
  }
  .front-label__story {
    position: absolute;
    left: 24px; top: 22px;
    width: 240px; height: 46px;
    transform-origin: 0 0;
    transform: translate(0, 240px) rotate(-90deg);
    font-size: 10px; line-height: 14px;
    color: var(--ink-soft);
  }
  .front-label__name {
    position: absolute;
    left: 110px; top: 96px;
    font-family: "Cormorant Garamond", Georgia, serif;
    font-weight: 500;
    font-size: 78px; line-height: 1;
    color: var(--ink);
  }
  .front-label__wine {
    position: absolute;
    left: 222px; top: 226px;
    font-family: "Arimo", Arial, sans-serif;
    font-size: 17px; line-height: 20px;
    color: var(--ink);
  }
  .front-label__volume {
    position: absolute;
    left: 38px; bottom: 46px;
    font-family: "Arimo", Arial, sans-serif;
    font-size: 15px;
    color: var(--ink);
  }
  .front-label__region {
    position: absolute;
    left: 222px; bottom: 46px;
    font-size: 12px;
    color: var(--ink-soft);
  }
</style>
</head>
<body>

  <div class="neck-collar" aria-label="Neck collar label"></div>

  <svg class="neck-medallion" viewBox="0 0 290 290" aria-label="Neck rondel">
    <defs>
      <linearGradient id="medallion-fill" x1="0" y1="0" x2="1" y2="1">
        <stop offset="0" stop-color="#2a3170"/>
        <stop offset="1" stop-color="#141939"/>
      </linearGradient>
      <path id="lower-arc" d="M 48 145 A 97 97 0 0 0 242 145"/>
    </defs>
    <circle cx="145" cy="145" r="143" fill="url(#medallion-fill)"/>
    <circle cx="145" cy="145" r="128" fill="none" stroke="#b9bbc0" stroke-width="1.5" stroke-dasharray="2 2"/>
    <circle cx="145" cy="158" r="58" fill="none" stroke="#c3c5c8" stroke-width="2"/>
    <text x="145" y="82" text-anchor="middle" font-family="Cormorant Garamond, Georgia, serif" font-weight="500" font-size="48" fill="#d5d7da">Mirren</text>
    <text font-family="Libre Caslon Text, Georgia, serif" font-size="15" fill="#d5d7da" letter-spacing="0.5">
      <textPath href="#lower-arc" startOffset="50%" text-anchor="middle">Ashvale Tasmania</textPath>
    </text>
  </svg>

  <section class="front-label" aria-label="Front label">
    <div class="front-label__frame"></div>
    <p class="front-label__story">Grown on a single slope in the cool east of the island, hand picked and aged on lees for three years before release for the table.</p>
    <div class="front-label__bar"></div>
    <h1 class="front-label__name">Mirren Hollow</h1>
    <p class="front-label__wine">2013<br>Chardonnay Pinot Noir</p>
    <p class="front-label__volume">750ml</p>
    <p class="front-label__region">Ashvale Tasmania</p>
  </section>

</body>
</html>
```